Velundra Jobs portal

Velundra Jobs is a job portal connecting job seekers and companies offering part time jobs in the Mena region, starting in the UAE. We would like to see designs that use the color blue. We have attached images to give an idea what the website should look like. When a company posts a job the job seekers are not allowed to see which company has posted a job. There should also be a coinvex gateway. On the landing page we want a catching picture that we will send.

Target Market(s)

Students and promotional workers

Logo Text

Velundra Jobs

Coding

Coded - Design and coding required

Number of Pages Required

4 page

Font styles to use
Sans Serif

Colors
33a6d7
0692cd
85cae6

```html
<!DOCTYPE html>
<html lang="en">
<head>
<meta charset="utf-8">
<title>Velundra Jobs</title>
<link rel="stylesheet" href="https://fonts.googleapis.com/css2?family=Open+Sans:wght@400;600&family=Raleway:wght@400;500&display=swap">
<style>
:root{
  --teal:#52c2c3;
  --teal-dark:#4ab8b9;
  --blue:#3765b8;
  --sky:#33a6d7;
  --orange:#f06a0c;
  --ink:#4a4a4a;
  --muted:#666;
  --page:#fcfaf4;
  --panel:#f4f4f4;
  --line:#e4e4e4;
  --star:#f5a623;
}
*{box-sizing:border-box;margin:0;padding:0}
html,body{width:1200px;height:1148px;overflow:hidden}
body{position:relative;background:var(--page);font-family:"Open Sans",sans-serif;color:var(--ink)}
.site-header{position:absolute;left:0;top:0;width:1200px;height:120px;background:linear-gradient(#fff,#f1f1f1);border-bottom:1px solid #dcdcdc}
.brand{position:absolute;left:96px;top:30px;display:flex;align-items:center;gap:10px;font-size:48px;color:var(--teal);font-weight:400;letter-spacing:-1px}
.brand-dot{width:14px;height:14px;background:var(--blue);border-radius:50%}
.main-nav{position:absolute;left:348px;top:49px;display:flex;font-family:"Raleway",sans-serif;font-size:15px;color:#444}
.main-nav a{color:inherit;text-decoration:none;padding:0 17px 0 0;height:22px}
.main-nav a+a{padding-left:17px;border-left:1px solid #ddd}
.tools{position:absolute;top:39px;left:860px;width:240px;height:40px}
.tools svg{position:absolute}
.badge{position:absolute;left:58px;top:4px;width:18px;height:18px;border-radius:50%;background:var(--orange);color:#fff;font-size:9px;line-height:18px;text-align:center}
.avatar{position:absolute;left:89px;top:0;width:40px;height:40px;border-radius:50%;background:var(--orange)}
.logout{position:absolute;left:144px;top:5px;width:96px;height:33px;background:var(--blue);color:#fff;font-family:"Raleway",sans-serif;font-size:15px;line-height:33px;text-align:center;border-radius:2px}
.category{position:absolute;left:96px;top:163px;width:265px;height:469px;background:var(--teal)}
.category h2{height:55px;background:var(--teal-dark);color:#fff;font-family:"Raleway",sans-serif;font-weight:400;font-size:18px;line-height:55px;padding-left:20px}
.category ul{list-style:none;padding:14px 0 0 20px}
.category li{color:#fff;font-size:14px;height:31px;line-height:20px;display:flex;align-items:center;gap:11px}
.category li::before{content:"";width:7px;height:7px;border:1.5px solid #fff;border-radius:50%}
.filter{position:absolute;left:395px;top:161px;width:707px;height:100px;background:var(--panel);border:1px solid var(--line)}
.field{position:absolute;top:31px;width:258px;height:40px;background:#fff;border:1px solid #e6e6e6;font-size:13px;line-height:38px;padding-left:15px;color:#333}
.field.keyword{left:23px}
.field.district{left:297px}
.field.district::after{content:"";position:absolute;right:14px;top:18px;border:5px solid transparent;border-top-color:#222}
.filter-btn{position:absolute;left:576px;top:31px;width:107px;height:40px;background:var(--teal);color:#fff;font-family:"Raleway",sans-serif;font-size:14px;line-height:40px;text-align:center;border-radius:2px}
.jobs{position:absolute;left:396px;top:282px;width:706px;height:416px;background:#fff;border:1px solid var(--line);overflow:hidden}
.jobs h1{height:70px;background:linear-gradient(#f1f1f1,#fafafa);font-weight:400;font-size:22px;line-height:66px;text-align:center;color:#444}
.job-table{border-collapse:collapse;width:692px;font-size:13px}
.job-table th{height:43px;font-weight:400;font-size:15px;text-align:left;color:#555;border-bottom:1px solid var(--line);background:#fbfbfb}
.job-table td{height:76px;color:#333}
.job-table tr:nth-child(even) td{background:#f4f4f4;height:74px}
.job-table th,.job-table td{padding-left:23px;border-right:1px solid #eee}
.job-table th:nth-child(2),.job-table td:nth-child(2){padding-left:29px}
.job-table th:nth-child(3),.job-table td:nth-child(3){padding-left:40px}
.job-table th:last-child,.job-table td:last-child{border-right:none;text-align:center;padding-left:0}
.job-title{font-size:15px;color:#444}
.apply{display:inline-block;width:96px;height:35px;line-height:35px;background:var(--blue);color:#fff;font-weight:600;font-size:13px;border-radius:2px}
.scrollbar{position:absolute;right:0;top:70px;width:14px;height:346px;background:#fff;border-left:1px solid #eee}
.scrollbar span{position:absolute;left:4px;top:22px;width:5px;height:58px;background:#555;border-radius:3px}
.mascot{position:absolute;left:81px;top:754px;width:228px;height:300px;border-radius:40% 40% 20% 20%;background:radial-gradient(ellipse at 50% 40%,rgba(130,180,200,.22),rgba(240,160,170,.12) 60%,rgba(252,250,244,0) 75%)}
.featured-title{position:absolute;left:396px;top:745px;font-size:32px;font-weight:400;color:#444}
.slider-arrows{position:absolute;left:1058px;top:755px}
.providers{position:absolute;left:399px;top:818px;display:flex;gap:15px}
.provider{width:165px}
.provider .photo{height:127px;box-shadow:0 1px 3px rgba(0,0,0,.25)}
.provider p{margin-top:13px;font-size:15px;color:#444}
.stars{margin-top:4px;font-size:12px;letter-spacing:1px;color:var(--star)}
.stars i{font-style:normal;color:#bbb}
.site-footer{position:absolute;left:0;top:1056px;width:1200px;height:92px;background:var(--sky);color:#fff;font-family:"Raleway",sans-serif;font-size:13px;text-align:center}
.site-footer .links{margin-top:25px}
.site-footer .copy{margin-top:8px}
</style>
</head>
<body>
<header class="site-header">
  <div class="brand"><span>velundra</span><span class="brand-dot"></span></div>
  <nav class="main-nav"><a href="#">About Us</a><a href="#">Contact Us</a></nav>
  <div class="tools">
    <svg width="28" height="28" style="left:2px;top:8px" viewBox="0 0 28 28"><circle cx="11" cy="11" r="8" fill="none" stroke="#333" stroke-width="3"/><line x1="17" y1="17" x2="25" y2="25" stroke="#333" stroke-width="3.5" stroke-linecap="round"/></svg>
    <svg width="30" height="30" style="left:44px;top:8px" viewBox="0 0 30 30"><path d="M7 21 V13 a8 8 0 0 1 16 0 V21 l3 3 H4 Z" fill="none" stroke="#444" stroke-width="2"/><path d="M12 26 a3 3 0 0 0 6 0" fill="none" stroke="#444" stroke-width="2"/></svg>
    <span class="badge">10</span>
    <span class="avatar"></span>
    <span class="logout">LOG OUT</span>
  </div>
</header>

<aside class="category">
  <h2>CATEGORY</h2>
  <ul>
    <li>Category 1 (33)</li><li>Category 2 (33)</li><li>Category 4 (303)</li><li>Category 5 (150)</li>
    <li>Category 6 (31)</li><li>Category 7 (201)</li><li>Category 1 (33)</li><li>Category 2 (33)</li>
    <li>Category 4 (303)</li><li>Category 5 (150)</li><li>Category 6 (31)</li><li>Category 7 (201)</li>
  </ul>
</aside>

<div class="mascot" role="img" aria-label="Faint mascot character illustration"></div>

<section class="filter">
  <div class="field keyword">Keyword</div>
  <div class="field district">District 1</div>
  <div class="filter-btn">FILTER JOB</div>
</section>

<section class="jobs">
  <h1>Find good a Job</h1>
  <table class="job-table">
    <tr><th style="width:224px">Job Title</th><th style="width:137px">Due Date</th><th style="width:163px">Provider Name</th><th></th></tr>
    <tr><td class="job-title">Front-end Developer</td><td>23-05-15</td><td>Provider 1</td><td><span class="apply">Apply Now</span></td></tr>
    <tr><td class="job-title">Front-end Developer</td><td>23-05-15</td><td>Provider 1</td><td><span class="apply">Apply Now</span></td></tr>
    <tr><td class="job-title">Front-end Developer</td><td>23-05-15</td><td>Provider 1</td><td><span class="apply">Apply Now</span></td></tr>
    <tr><td class="job-title">Front-end Developer</td><td>23-05-15</td><td>Provider 1</td><td><span class="apply">Apply Now</span></td></tr>
  </table>
  <div class="scrollbar"><span></span></div>
</section>

<h2 class="featured-title">Featured Job Providers</h2>
<svg class="slider-arrows" width="46" height="28" viewBox="0 0 46 28"><polyline points="14,2 3,14 14,26" fill="none" stroke="#555" stroke-width="2"/><polyline points="32,2 43,14 32,26" fill="none" stroke="#555" stroke-width="2"/></svg>

<div class="providers">
  <div class="provider"><div class="photo" role="img" aria-label="Office handshake photo" style="background:linear-gradient(135deg,#e8e2d8,#6b5a52 55%,#f0ede8)"></div><p>Duis aute irure dolor in</p><div class="stars">★★★<i>☆☆</i></div></div>
  <div class="provider"><div class="photo" role="img" aria-label="Business meeting photo" style="background:linear-gradient(135deg,#dfe8ee,#7d8a92 50%,#c9d4da)"></div><p>Duis aute irure dolor in</p><div class="stars">★★★<i>☆☆</i></div></div>
  <div class="provider"><div class="photo" role="img" aria-label="Tablet in hand photo" style="background:linear-gradient(135deg,#f3f3f3,#8a9aa8 50%,#e4e4e4)"></div><p>Duis aute irure dolor in</p><div class="stars">★★★<i>☆☆</i></div></div>
  <div class="provider"><div class="photo" role="img" aria-label="Team working at laptop photo" style="background:linear-gradient(135deg,#5d7a5a,#3a8fbf 50%,#d8d2c6)"></div><p>Duis aute irure dolor in</p><div class="stars">★★★<i>☆☆</i></div></div>
</div>

<footer class="site-footer">
  <div class="links">Privacy Policy | Terms of Service | Customer Support</div>
  <div class="copy">© 2015 Velundra . all copy rights reserved</div>
</footer>
</body>
</html>
```